Business Card Design for Flood Rescue 360 - Property Restoration Professionals

I need a business card designed for Flood Rescue 360. We are a full-service property restoration solution. Providing water, fire, smoke & storm restoration as well as mold remediation and full remodel or reconstruction to homes and businesses across Dallas-Fort Worth, TX.
Target Market(s)
home and business owners with insurance covered property damage from water, fire or storm related damage
Industry/Entity Type
property restoration
Contact Information for Business Card
Marcus Pelley General Manager Cell: 214-555-0193 Office: 469-555-0148 email: Marcus@FloodRescue360.example services: Water, Fire, Mold, Reconstruction Tagline: Fast Help When Water Strikes!
Look and feel
Each slider illustrates characteristics of the customer's brand and the style your logo design should communicate.

```html
<!DOCTYPE html>
<html lang="en">
<head>
<meta charset="utf-8">
<title>Flood Rescue 360 – Business Card</title>
<link href="https://fonts.googleapis.com/css2?family=Montserrat:wght@400;500;700;800&display=swap" rel="stylesheet">
<style>
  :root {
    --backdrop: #d5d7d8;
    --brand-blue: #13a3dc;
    --deep-blue: #1594cc;
    --charcoal: #3b3d3f;
    --paper: #fbfbfa;
    --ink: #3a3a3a;
  }
  * { margin: 0; padding: 0; box-sizing: border-box; }
  html, body { width: 1200px; height: 829px; overflow: hidden; }
  body {
    background: var(--backdrop);
    font-family: "Montserrat", sans-serif;
    position: relative;
  }
  .card {
    position: absolute;
    top: 260px;
    width: 540px;
    height: 309px;
    overflow: hidden;
    box-shadow: 0 10px 30px rgba(0,0,0,0.18);
  }
  /* Front */
  .card--front { left: 40px; background: var(--paper); }
  .card__wave { position: absolute; inset: 0; }
  .front-brand {
    position: absolute;
    left: 30px; top: 92px;
    width: 222px;
    font-weight: 700;
    font-size: 23px;
    line-height: 1;
    white-space: nowrap;
    color: var(--brand-blue);
  }
  .divider {
    position: absolute;
    left: 266px; top: 40px;
    width: 1px; height: 150px;
    background: #c9c9c9;
  }
  .contact {
    position: absolute;
    left: 282px; top: 46px;
    color: var(--ink);
  }
  .contact__name {
    font-weight: 700;
    font-size: 21px;
    color: var(--brand-blue);
    text-transform: uppercase;
    letter-spacing: 0.5px;
  }
  .contact__role { font-size: 13px; margin-bottom: 12px; }
  .contact__list { list-style: none; font-size: 12.5px; line-height: 1.65; }
  .contact__list li { display: flex; align-items: center; gap: 7px; }
  .contact__list svg { width: 11px; height: 11px; fill: var(--brand-blue); flex: none; }

  /* Back */
  .card--back { left: 620px; background: var(--brand-blue); color: #fff; }
  .back-brand {
    position: absolute;
    left: 0; right: 0; top: 98px;
    text-align: center;
    font-weight: 700;
    font-size: 38px;
    line-height: 1;
    white-space: nowrap;
    color: #fff;
  }
  .services {
    position: absolute;
    left: 0; right: 0; top: 180px;
    text-align: center;
    font-size: 14px;
    letter-spacing: 1px;
  }
  .tagline-band {
    position: absolute;
    left: 0; right: 0; top: 214px;
    height: 30px;
    background: var(--charcoal);
    display: flex; align-items: center; justify-content: center;
  }
  .tagline {
    font-weight: 700;
    font-size: 14px;
    color: var(--brand-blue);
    letter-spacing: 0.5px;
  }
</style>
</head>
<body>
  <section class="card card--front" aria-label="Business card front">
    <svg class="card__wave" viewBox="0 0 540 309" preserveAspectRatio="none" aria-hidden="true">
      <path d="M0,178 C120,235 300,285 540,296 L540,309 L0,309 Z" fill="var(--deep-blue)"/>
      <path d="M190,250 C300,280 420,292 540,294 L540,302 C420,299 300,288 190,250 Z" fill="var(--charcoal)"/>
    </svg>
    <div class="front-brand">Flood Rescue 360</div>
    <div class="divider"></div>
    <div class="contact">
      <div class="contact__name">Marcus Pelley</div>
      <div class="contact__role">General Manager</div>
      <ul class="contact__list">
        <li><svg viewBox="0 0 12 12"><path d="M2 1h3l1 3-1.5 1a7 7 0 0 0 2.5 2.5L8 6l3 1v3c0 .6-.4 1-1 1A9 9 0 0 1 1 2c0-.6.4-1 1-1z"/></svg>469-555-0148</li>
        <li><svg viewBox="0 0 12 12"><path d="M3.5 0h5c.6 0 1 .4 1 1v10c0 .6-.4 1-1 1h-5c-.6 0-1-.4-1-1V1c0-.6.4-1 1-1zm.5 2v7h4V2z"/></svg>214-555-0193</li>
        <li><svg viewBox="0 0 12 12"><path d="M0 2h12v8H0zm1 1v.5l5 3.2 5-3.2V3z"/></svg>Marcus@FloodRescue360.example</li>
        <li><svg viewBox="0 0 12 12"><circle cx="6" cy="6" r="5.5"/></svg>www.FloodRescue360.example</li>
      </ul>
    </div>
  </section>

  <section class="card card--back" aria-label="Business card back">
    <div class="back-brand">Flood Rescue 360</div>
    <div class="services">Water • Fire • Mold • Reconstruction</div>
    <div class="tagline-band">
      <span class="tagline">Fast Help When Water Strikes!</span>
    </div>
  </section>
</body>
</html>
```